Business Card Design

We need a business card designed for our new company. Prefer a black card with white logo & writing.

Contact Information for Business Card

Ted Galloway, address: 7-4812 Fernhollow Road, Abbotsford, BC, V3K 8R2, Office Phone: 604-712-3390, Cell: 604-947-2164, Email: ted@resinworkshub.ca

Colors

Designer to choose only greyscale colors for use in the design.

```html
<!DOCTYPE html>
<html lang="en">
<head>
<meta charset="UTF-8">
<title>Resinworks Hub — Business Card</title>
<link href="https://fonts.googleapis.com/css2?family=Montserrat:wght@400;500;600;700;800&display=swap" rel="stylesheet">
<style>
  :root {
    --backdrop: #d9d7d4;
    --card-dark: #262626;
    --card-light: #ffffff;
    --ink-light: #ffffff;
    --ink-soft: #e6e6e6;
    --ink-dark: #232323;
    --shadow: rgba(0, 0, 0, 0.35);
  }
  * { margin: 0; padding: 0; box-sizing: border-box; }
  html, body {
    width: 900px; height: 1200px; overflow: hidden;
    background: var(--backdrop);
    font-family: "Montserrat", Arial, sans-serif;
  }
  .stage { position: relative; width: 900px; height: 1200px; }
  .card {
    position: absolute;
    background: var(--card-dark);
    border-radius: 22px;
    overflow: hidden;
    box-shadow: 0 8px 22px var(--shadow);
  }
  .card--front { left: 80px; top: 131px; width: 742px; height: 440px; }
  .card--back { left: 78px; top: 640px; width: 744px; height: 438px; }
  .front-art { position: absolute; inset: 0; width: 742px; height: 440px; }

  .holder { position: absolute; left: 36px; top: 50px; color: var(--ink-light); }
  .holder__name { font-size: 24px; font-weight: 700; letter-spacing: 0.2px; }
  .holder__role { font-size: 15px; font-weight: 400; color: var(--ink-soft); margin-top: 4px; }

  .address {
    position: absolute; left: 38px; top: 234px;
    font-size: 16px; line-height: 21px; color: var(--ink-soft); font-style: normal;
  }
  .contacts { position: absolute; left: 36px; top: 298px; list-style: none; }
  .contacts__item {
    display: flex; align-items: center; gap: 12px;
    font-size: 15.5px; color: var(--ink-soft); height: 26px;
  }
  .contacts__item:nth-child(2) { margin-top: 4px; }
  .contacts__icon { width: 17px; height: 17px; flex: none; fill: var(--ink-light); }

  .brand {
    position: absolute; font-weight: 800; text-transform: uppercase;
    text-align: center; white-space: nowrap; letter-spacing: 0.5px;
  }
  .brand__line { display: block; }
  .brand--front {
    left: 477px; width: 240px; top: 212px;
    font-size: 26px; line-height: 32px; color: var(--ink-dark);
  }
  .brand--back {
    left: 0; right: 0; top: 172px;
    font-size: 50px; line-height: 58px; color: var(--ink-light);
  }
</style>
</head>
<body>
<main class="stage">
  <section class="card card--front" aria-label="Card front">
    <svg class="front-art" viewBox="0 0 742 440" aria-hidden="true">
      <path d="M742 0 H622 C500 40 420 150 424 235 C428 320 505 400 612 440 H742 Z" fill="var(--card-light)"/>
      <path d="M588 30 C470 85 405 175 410 250 C415 325 470 385 575 432" fill="none" stroke="var(--card-light)" stroke-width="4"/>
    </svg>

    <div class="holder">
      <h1 class="holder__name">Ted Galloway</h1>
      <p class="holder__role">Owner</p>
    </div>

    <address class="address">7-4812 Fernhollow Road,<br>Abbotsford, BC, V3K 8R2</address>

    <ul class="contacts">
      <li class="contacts__item">
        <svg class="contacts__icon" viewBox="0 0 24 24"><path d="M6.6 10.8a15.1 15.1 0 0 0 6.6 6.6l2.2-2.2a1 1 0 0 1 1-.25 11.4 11.4 0 0 0 3.6.57 1 1 0 0 1 1 1V20a1 1 0 0 1-1 1A17 17 0 0 1 3 4a1 1 0 0 1 1-1h3.5a1 1 0 0 1 1 1c0 1.25.2 2.45.57 3.6a1 1 0 0 1-.25 1z"/></svg>
        604-712-3390
      </li>
      <li class="contacts__item">
        <svg class="contacts__icon" viewBox="0 0 24 24"><path d="M7 1h10a2 2 0 0 1 2 2v18a2 2 0 0 1-2 2H7a2 2 0 0 1-2-2V3a2 2 0 0 1 2-2zm0 3v14h10V4zm5 15.5a1.2 1.2 0 1 0 0 2.4 1.2 1.2 0 0 0 0-2.4z"/></svg>
        604-947-2164
      </li>
      <li class="contacts__item">
        <svg class="contacts__icon" viewBox="0 0 24 24"><path d="M2 5h20v2l-10 6L2 7zm0 4.3l10 6 10-6V19H2z"/></svg>
        ted@resinworkshub.ca
      </li>
      <li class="contacts__item">
        <svg class="contacts__icon" viewBox="0 0 24 24"><path d="M12 2a10 10 0 1 0 0 20 10 10 0 0 0 0-20zm-1 17.9A8 8 0 0 1 4.1 10l4.9 4.9V16a2 2 0 0 0 2 2zm6.9-2.5A2 2 0 0 0 16 16h-1v-3a1 1 0 0 0-1-1H8v-2h2a1 1 0 0 0 1-1V7h2a2 2 0 0 0 2-2v-.4a8 8 0 0 1 2.9 12.8z"/></svg>
        www.resinworkshub.ca
      </li>
    </ul>

    <p class="brand brand--front"><span class="brand__line">Resinworks</span><span class="brand__line">Hub</span></p>
  </section>

  <section class="card card--back" aria-label="Card back">
    <p class="brand brand--back"><span class="brand__line">Resinworks</span><span class="brand__line">Hub</span></p>
  </section>
</main>
</body>
</html>
```